Psychotherapy, Life Coaching, Writer, Motivational Speaker

I am a psychotherapist, life coach, writer and speaker on health and wellness issues. I am a humanist - who believes that we are born to self-actualize - but life - changes that course. That we develop armor and coping mechanisms that divert our growth. I help people examine their road blocks to happiness. My business is unique in that I do concierge therapy. I work intensively - with multi-day sessions, I work internationally through tele-therapy - and traditionally - in an office space. My work is tailored to your needs.

Target Market(s)

Broad

Industry/Entity Type

Health

Contact Information for Business Card

Listen And Grow
Sam Perriton
248 East 39th Street
New York, NY 10027
(305) 555-0173

Requirements
Must have
• Clean lines... not too busy...
• FB page listing: Listen And Grow
• my Web page: www.listenandgrow-example.com
Nice to have
• I would love to be able to list the services: Psychotherapist, Life Coach, Motivational Speaker and Writer - but also don't want a crazy crowded card. Feel free to use the back for description.
Should not have
• Stay away from corny imagery - lotus flowers, zen, lily pond, clouds.

```html
<!DOCTYPE html>
<html lang="en">
<head>
<meta charset="utf-8">
<title>Listen And Grow – Business Card</title>
<link href="https://fonts.googleapis.com/css2?family=Lato:wght@400;700&display=swap" rel="stylesheet">
<style>
  :root {
    --backdrop: #e4e5e7;
    --card: #ffffff;
    --brand-blue: #4a78b5;
    --band-blue: #3b67a6;
    --ink: #1c1c1c;
    --accent-dark: #151515;
    --accent-fade: #efefef;
  }
  * { box-sizing: border-box; margin: 0; padding: 0; }
  html, body { width: 1200px; height: 720px; overflow: hidden; }
  body {
    background: var(--backdrop);
    font-family: "Lato", Arial, sans-serif;
    color: var(--ink);
    position: relative;
  }
  .card {
    position: absolute;
    top: 241px;
    width: 419px;
    height: 239px;
    background: var(--card);
    border-radius: 14px;
    overflow: hidden;
  }
  .card--front { left: 148px; }
  .card--back { left: 633px; }
  .abs { position: absolute; white-space: nowrap; }

  /* Front */
  .front__brand {
    right: 18px; top: 16px;
    font-size: 23px; font-weight: 700; color: var(--brand-blue);
  }
  .front__name { left: 18px; top: 79px; font-size: 14px; }
  .front__name strong { font-size: 17px; color: var(--brand-blue); }
  .front__role { left: 18px; top: 100px; font-size: 13.5px; }
  .front__accent {
    left: 0; top: 122px; width: 295px; height: 24px;
    background: linear-gradient(90deg, var(--accent-dark) 0%, var(--accent-dark) 35%, var(--accent-fade) 100%);
  }
  .contact-list { left: 19px; top: 160px; list-style: none; font-size: 13.5px; line-height: 16px; }
  .contact-list li { display: flex; align-items: center; gap: 4px; }
  .contact-list svg { flex: none; }
  .social-mark { width: 10px; height: 10px; background: var(--band-blue); border-radius: 2px; margin-right: 1px; }
  .front__address { right: 11px; top: 191px; font-size: 12.5px; line-height: 15.5px; text-align: right; font-style: normal; }

  /* Back */
  .back__band { left: 0; top: 0; }
  .back__brand { left: 17px; top: 57px; font-size: 21px; font-weight: 700; color: var(--brand-blue); }
  .service-list { left: 17px; top: 97px; list-style: none; font-size: 13px; line-height: 16px; }
  .back__appointment { left: 19px; top: 165px; font-size: 13.5px; }
</style>
</head>
<body>

<section class="card card--front" aria-label="Card front">
  <div class="abs front__brand">Listen And Grow</div>

  <div class="abs front__name"><strong>Sam Perriton,</strong> LMHC, NCC</div>
  <div class="abs front__role">Psychotherapist.</div>

  <div class="abs front__accent" role="img" aria-label="Black decorative sweep graphic"></div>

  <ul class="abs contact-list">
    <li>
      <svg width="11" height="10" viewBox="0 0 11 10" aria-hidden="true"><path d="M1 3 C1 1 3 1 5.5 1 C8 1 10 1 10 3 L8 4 L7 2.8 L4 2.8 L3 4 Z M2.5 5 L8.5 5 L9.5 9 L1.5 9 Z" fill="var(--band-blue)"/></svg>
      <span>(305) 555-0173</span>
    </li>
    <li>
      <svg width="11" height="9" viewBox="0 0 11 9" aria-hidden="true"><rect x="0.5" y="0.5" width="10" height="8" fill="var(--band-blue)"/><path d="M0.5 0.5 L5.5 5 L10.5 0.5" stroke="#fff" fill="none"/></svg>
      <span>sperriton.mail@example.com</span>
    </li>
    <li>
      <svg width="11" height="11" viewBox="0 0 11 11" aria-hidden="true"><circle cx="5.5" cy="5.5" r="4.8" fill="none" stroke="var(--band-blue)" stroke-width="1.2"/><ellipse cx="5.5" cy="5.5" rx="2" ry="4.8" fill="none" stroke="var(--band-blue)"/><line x1="0.7" y1="5.5" x2="10.3" y2="5.5" stroke="var(--band-blue)"/></svg>
      <span>www.listenandgrow-example.com</span>
    </li>
    <li>
      <span class="social-mark" aria-hidden="true"></span>
      <span>Listen And Grow</span>
    </li>
  </ul>

  <address class="abs front__address">
    248 East 39th Street<br>New York, NY 10027
  </address>
</section>

<section class="card card--back" aria-label="Card back">
  <svg class="abs back__band" width="419" height="239" viewBox="0 0 419 239" aria-hidden="true">
    <path d="M376 0 C 378 22 386 45 393 70 C 400 98 402 128 397 155 C 392 185 383 212 375 239 L419 239 L419 0 Z" fill="var(--band-blue)"/>
  </svg>

  <div class="abs back__brand">Listen And Grow</div>
  <ul class="abs service-list">
    <li>Psychotherapy,</li>
    <li>Coaching,</li>
    <li>Wellness Media</li>
  </ul>
  <div class="abs back__appointment">Your Next Appoinment is at...................... at.............. am/pm</div>
</section>

</body>
</html>
```